business card - Helicopter Flight Services, Flight School, etc.

We need a business card design for a new helicopter service.

We offer Helicopter Flight Services, Aerial Filming & Photography, Flight School, and Helicopter Tours. In that order.

Summit BladeAir, Inc.
Dennis Tollerby
SummitBladeair@Kestmail.com
626-418-7352

Based at the Brenwick Airport in Van Nuys, CA. The final design should communicate integrity and safety. Pictures or logos at your discretion.

Card back side - surprise me.

```html
<!DOCTYPE html>
<html lang="en">
<head>
<meta charset="utf-8">
<title>Summit BladeAir, Inc. – Business Card</title>
<link href="https://fonts.googleapis.com/css2?family=Open+Sans:wght@400;600&display=swap" rel="stylesheet">
<style>
  :root {
    --backdrop: #4a433f;
    --card: #0d0d0e;
    --card-edge: #1b1b1d;
    --accent-blue: #3f86d4;
    --ink-white: #f2f2f2;
    --ink-silver: #c9cacc;
    --divider: #2a2a2e;
  }
  * { box-sizing: border-box; margin: 0; padding: 0; }
  html, body {
    width: 1200px; height: 900px; overflow: hidden;
    background: var(--backdrop);
    font-family: "Open Sans", Arial, sans-serif;
  }
  .stage {
    position: relative; width: 1200px; height: 900px;
    display: flex; align-items: center; justify-content: center; gap: 40px;
  }
  .card {
    position: relative; width: 540px; height: 310px;
    background: var(--card);
    border: 1px solid var(--card-edge);
    box-shadow: 0 12px 30px rgba(0,0,0,0.45);
  }
  /* Front */
  .card-front .brand {
    position: absolute; left: 40px; top: 0; bottom: 0; width: 250px;
    display: flex; align-items: center; gap: 12px;
  }
  .brand-dot {
    flex: none; width: 22px; height: 22px; border-radius: 50%;
    background: var(--accent-blue);
  }
  .brand-name {
    font-size: 21px; font-weight: 600; line-height: 1.2;
    color: var(--accent-blue); letter-spacing: 0.5px;
  }
  .card-front .divider {
    position: absolute; left: 300px; top: 40px; bottom: 100px;
    width: 1px; background: var(--divider);
  }
  .contact {
    position: absolute; left: 322px; top: 60px;
  }
  .contact-name {
    font-size: 19px; font-weight: 600; color: var(--accent-blue);
    margin-bottom: 18px;
  }
  .contact-line {
    display: flex; align-items: center; gap: 10px;
    font-size: 13px; color: var(--ink-white); margin-bottom: 6px;
  }
  .contact-line svg { flex: none; width: 12px; height: 12px; fill: var(--accent-blue); }
  /* Back */
  .card-back .brand {
    position: absolute; left: 40px; top: 0; bottom: 0; width: 230px;
    display: flex; align-items: center; gap: 12px;
  }
  .card-back .brand-dot { background: var(--ink-silver); }
  .card-back .brand-name { color: var(--ink-silver); }
  .services {
    position: absolute; left: 290px; top: 70px;
    list-style: none;
    font-size: 14px; line-height: 1.45; color: var(--ink-white);
  }
</style>
</head>
<body>
  <main class="stage">
    <section class="card card-front">
      <div class="brand">
        <span class="brand-dot"></span>
        <span class="brand-name">Summit BladeAir, Inc.</span>
      </div>
      <div class="divider"></div>
      <div class="contact">
        <p class="contact-name">Dennis Tollerby</p>
        <p class="contact-line">
          <svg viewBox="0 0 24 24" aria-hidden="true"><path d="M6.6 10.8a15.1 15.1 0 0 0 6.6 6.6l2.2-2.2a1 1 0 0 1 1-.25 11.4 11.4 0 0 0 3.6.57 1 1 0 0 1 1 1V20a1 1 0 0 1-1 1A17 17 0 0 1 3 4a1 1 0 0 1 1-1h3.5a1 1 0 0 1 1 1c0 1.25.2 2.45.57 3.57a1 1 0 0 1-.25 1z"/></svg>
          626-418-7352
        </p>
        <p class="contact-line">
          <svg viewBox="0 0 24 24" aria-hidden="true"><path d="M2 5h20v14H2z M2 5l10 8 10-8" /></svg>
          SummitBladeair@Kestmail.com
        </p>
      </div>
    </section>

    <section class="card card-back">
      <div class="brand">
        <span class="brand-dot"></span>
        <span class="brand-name">Summit BladeAir, Inc.</span>
      </div>
      <ul class="services">
        <li>Helicopter Flight Services,</li>
        <li>Aerial Filming &amp; Photography,</li>
        <li>Flight School,</li>
        <li>Helicopter Tours</li>
      </ul>
    </section>
  </main>
</body>
</html>
```